Corvane Lending Partners. Professional and Established Company

A full service finance company specializing in obtaining capital for small business. Business Lending advisor, helping small business owners access the capital they need to launch, grow, or sustain their business. Many of our programs offer flexible guidelines to overcome common obstacles such as credit score, credit history, and time in business, financials, and industry type. Our streamlined funding process makes getting a business loan, business line of credit, stated income commercial real estate loan, a smooth and stress free experience.SOME OF THE MOST COMMON NEEDS FOR BUSINESS CAPITAL:• Working Capital• Debt Consolidations (loans, merchant cash advances, etc.)• Payroll• Operating Expenses• Inventory• Equipment Financing• Commercial Real Estate (Purchase, Fix & Flip, Rehab, Renovations)• Business Acquisitions• Business ExpansionWe like the websites:www.quillmorecf.com they are in the same industry and provide the same servicesWe are wanting to be able to update when we do press releases and such using Word Press. Our look should be very professional and we will be adding Our Team Professional Bios and Headshots.

Industry/Entity Type

Finance

Number of Pages Required

5+ page

Font styles to use
Serif
Sans Serif

Requirements
Must have
• We want to copy quillmorecf.com
• We need:
• Home Page
• About Us
• Loan Programs
• Loan Criteria
• News
• Apply Now
• Contact
Nice to have
• See quillmorecf.com
Should not have
• Need professional design. Nothing bright or abstract

```html
<!DOCTYPE html>
<html lang="en">
<head>
<meta charset="utf-8">
<title>Corvane Lending Partners</title>
<link rel="stylesheet" href="https://fonts.googleapis.com/css2?family=Cinzel:wght@400;700&family=Open+Sans:wght@400;600;700&display=swap">
<style>
:root{
  --blue:#2a5ea6;
  --blue-dark:#1d4a8a;
  --ink:#222;
  --text:#666;
  --muted:#8a8a8a;
  --pale:#eef2f6;
  --footer:#0d0d0d;
  --white:#fff;
}
*{box-sizing:border-box;margin:0;padding:0}
html,body{width:1200px;height:4986px;overflow:hidden;background:var(--white)}
body{font-family:"Open Sans",Arial,sans-serif;color:var(--text);position:relative}
.abs{position:absolute}
.serif{font-family:"Cinzel",Georgia,serif;font-weight:400;color:var(--ink);letter-spacing:2px}
.section-title{position:absolute;left:0;width:1200px;text-align:center;font-size:50px}
/* header */
.site-header{position:absolute;top:0;left:0;width:1200px;height:103px;background:var(--white)}
.brand{position:absolute;left:112px;top:16px;color:var(--blue);font-family:"Cinzel",Georgia,serif;font-weight:700;line-height:1}
.brand .big{display:block;font-size:40px;letter-spacing:3px}
.brand .small{display:block;font-size:13.5px;letter-spacing:2.4px;margin-top:4px}
.topbar{position:absolute;top:22px;right:110px;font-size:14px;color:#333;display:flex;align-items:center;gap:8px}
.topbar svg{width:14px;height:14px;fill:var(--blue)}
.topbar .sep{margin:0 8px;color:#999}
.nav{position:absolute;top:62px;left:430px;display:flex;gap:26px;font-size:15px;color:#222;align-items:center}
.nav .active{color:var(--blue)}
.nav svg{width:16px;height:16px;margin-left:12px}
/* hero */
.hero{position:absolute;top:103px;left:0;width:1200px;height:578px;background:linear-gradient(115deg,#9ec3e6 0%,#5d8fc7 30%,#2f5f9e 60%,#1c3f72 100%)}
.hero h1{position:absolute;left:114px;top:160px;font-family:"Cinzel",Georgia,serif;font-weight:400;font-size:54px;color:var(--white);letter-spacing:2px}
.hero p{position:absolute;left:114px;top:253px;width:460px;font-size:18px;line-height:30px;color:var(--white)}
.btn-ghost{position:absolute;left:116px;top:359px;width:180px;height:48px;border:2px solid var(--white);border-radius:24px;color:var(--white);font-size:13px;font-weight:700;display:flex;align-items:center;justify-content:center;letter-spacing:.5px}
.dots{position:absolute;left:572px;top:504px;display:flex;gap:5px}
.dots span{width:10px;height:10px;border-radius:50%;background:rgba(255,255,255,.55)}
.dots span:first-child{background:var(--white)}
/* welcome */
.intro{position:absolute;left:225px;top:868px;width:750px;text-align:center;font-size:14px;line-height:25px;color:var(--text)}
.service{position:absolute;width:240px;text-align:center}
.service svg{width:62px;height:62px;stroke:var(--blue);fill:none;stroke-width:2.4;stroke-linecap:round;stroke-linejoin:round;display:block;margin:0 auto}
.service h3{font-size:18px;font-weight:400;color:#222;margin-top:14px}
.service p{font-size:13.5px;line-height:22px;color:var(--muted);margin-top:10px}
.btn-outline{position:absolute;width:190px;height:58px;border:2px solid var(--blue);border-radius:29px;color:var(--blue);font-size:14px;font-weight:700;display:flex;align-items:center;justify-content:center;letter-spacing:.5px}
/* about */
.about{position:absolute;top:1689px;left:0;width:1200px;height:422px;background:var(--pale)}
.about h2{position:absolute;left:113px;top:54px;font-size:50px}
.about p{position:absolute;left:113px;top:138px;width:440px;font-size:14px;line-height:24px;color:var(--text)}
.btn-small{position:absolute;left:113px;top:309px;width:143px;height:44px;border:2px solid var(--blue);border-radius:22px;color:var(--blue);font-size:13px;font-weight:700;display:flex;align-items:center;justify-content:center}
.about .photo{position:absolute;left:598px;top:0;width:602px;height:422px;background:linear-gradient(135deg,#cfd8e0 0%,#8fa3b5 45%,#4d6275 100%)}
/* loans */
.loan-photo{position:absolute;height:273px}
.loan-label{position:absolute;width:396px;text-align:center;font-size:22px;letter-spacing:1px}
/* apply */
.apply{position:absolute;top:3341px;left:0;width:1200px;height:385px;background:var(--blue)}
.apply h2{position:absolute;left:0;top:94px;width:1200px;text-align:center;color:var(--white);font-size:50px}
.apply .lead{position:absolute;left:0;top:168px;width:1200px;text-align:center;color:var(--white);font-size:20px;font-weight:600}
.apply .field{position:absolute;left:296px;top:232px;width:536px;height:57px;background:var(--white);font-size:14px;color:#333;padding-left:22px;display:flex;align-items:center}
.apply .go{position:absolute;left:832px;top:232px;width:72px;height:57px;background:#111;display:flex;align-items:center;justify-content:center}
/* team */
.member{position:absolute;width:250px;text-align:center}
.avatar{width:226px;height:226px;margin:0 auto;border-radius:50%;border:6px solid #e3e3e3;background:linear-gradient(180deg,#d9dde2 0%,#9aa3ad 100%)}
.member h3{font-size:21px;font-weight:600;color:#222;margin-top:26px}
.member .role{font-size:14px;font-style:italic;color:#555;margin-top:4px}
.member p{font-size:13.5px;line-height:22px;color:var(--muted);margin-top:12px;padding:0 10px}
/* footer */
.site-footer{position:absolute;top:4431px;left:0;width:1200px;height:555px;background:var(--footer)}
.site-footer h4{position:absolute;top:104px;font-family:"Cinzel",Georgia,serif;font-weight:400;font-size:24px;color:var(--white);letter-spacing:1px}
.input{position:absolute;background:var(--white);height:27px;font-size:12px;color:#444;padding-left:8px;display:flex;align-items:center}
.textarea{align-items:flex-start;padding-top:7px}
.submit{position:absolute;left:632px;top:372px;width:113px;height:43px;border-radius:22px;background:var(--blue);color:var(--white);font-size:13px;font-weight:700;display:flex;align-items:center;justify-content:center}
.info{position:absolute;left:801px;display:flex;align-items:center;gap:18px;color:var(--white);font-size:14px;line-height:22px}
.info .ring{width:38px;height:38px;border:1px solid #666;border-radius:50%;display:flex;align-items:center;justify-content:center;flex:none}
.info svg{width:16px;height:16px;fill:#bbb}
.social{position:absolute;left:802px;top:362px;display:flex;gap:10px}
.social span{width:32px;height:32px;border-radius:50%;background:var(--blue)}
.rule{position:absolute;left:113px;top:455px;width:974px;height:1px;background:#333}
.copy{position:absolute;left:0;top:490px;width:1200px;text-align:center;font-size:13px;color:#bbb}
</style>
</head>
<body>

<header class="site-header">
  <div class="brand"><span class="big">CORVANE</span><span class="small">LENDING PARTNERS</span></div>
  <div class="topbar">
    <svg viewBox="0 0 24 24"><path d="M6.6 10.8a15 15 0 0 0 6.6 6.6l2.2-2.2c.3-.3.7-.4 1-.2 1.1.4 2.3.6 3.6.6.6 0 1 .4 1 1V20c0 .6-.4 1-1 1A17 17 0 0 1 3 4c0-.6.4-1 1-1h3.5c.6 0 1 .4 1 1 0 1.3.2 2.5.6 3.6.1.3 0 .7-.2 1z"/></svg>
    <span>1 800 555 0142</span><span class="sep">|</span>
    <svg viewBox="0 0 24 24"><path d="M2 5h20v14H2z M2 5l10 8 10-8" fill="var(--blue)"/><path d="M3 6l9 7 9-7" stroke="#fff" stroke-width="1.6" fill="none"/></svg>
    <span>info@corvanelending.com</span>
  </div>
  <nav class="nav">
    <span class="active">Home</span><span>About Us</span><span>Loan Programs</span><span>Loan Criteria</span><span>News</span><span>Apply Now</span><span>Contact</span>
    <svg viewBox="0 0 24 24" fill="none" stroke="#222" stroke-width="3"><circle cx="10" cy="10" r="7"/><path d="M15 15l7 7"/></svg>
  </nav>
</header>

<section class="hero" role="img" aria-label="Upward view of glass office towers against a blue sky">
  <h1>LENDING PARTNERS</h1>
  <p>We are a full service finance company specializing in obtaining capital for small business.</p>
  <div class="btn-ghost">GET MORE INFO</div>
  <div class="dots"><span></span><span></span><span></span><span></span></div>
</section>

<h2 class="section-title serif" style="top:778px">WELCOME TO CORVANE</h2>
<p class="intro">Nemo enim ipsam voluptatem quia voluptas sit aspernatur aut odit aut fugit, sed quia consequuntur magni dolores eos qui ratione voluptatem sequi nesciunt. Neque porro quisquam est, qui dolorem ipsum quia dolor sit amet, consectetur, adipisci velit, sed quia non numquam eius modi tempora incidunt ut labore et dolore magnam aliquam.</p>

<div class="service" style="left:103px;top:1022px">
  <svg viewBox="0 0 64 64"><rect x="6" y="16" width="52" height="32" rx="2"/><rect x="11" y="21" width="42" height="22"/><circle cx="32" cy="32" r="7"/></svg>
  <h3>Working Capital</h3><p>Ut enim ad minima veniam quis nostrum exercitationem ulla</p>
</div>
<div class="service" style="left:355px;top:1022px">
  <svg viewBox="0 0 64 64"><path d="M16 6h24l10 10v42H16z"/><path d="M40 6v10h10"/><path d="M23 28h20M23 36h20M23 44h14"/></svg>
  <h3>Payroll</h3><p>Ut enim ad minima veniam quis nostrum exercitationem ulla</p>
</div>
<div class="service" style="left:605px;top:1022px">
  <svg viewBox="0 0 64 64"><path d="M32 8v48M20 56h24M10 16h44"/><path d="M10 16l-7 18h14zM54 16l-7 18h14z"/><path d="M3 34a7 5 0 0 0 14 0M47 34a7 5 0 0 0 14 0"/></svg>
  <h3>Debt Consolidations</h3><p>Ut enim ad minima veniam quis nostrum exercitationem ulla</p>
</div>
<div class="service" style="left:861px;top:1022px">
  <svg viewBox="0 0 64 64"><circle cx="24" cy="36" r="12"/><circle cx="24" cy="36" r="5"/><circle cx="46" cy="18" r="9"/><circle cx="46" cy="18" r="3"/><path d="M24 20v4M24 48v4M8 36h4M36 36h4M46 5v4M46 27v4M33 18h4M55 18h4"/></svg>
  <h3>Operating Expenses</h3><p>Ut enim ad minima veniam quis nostrum exercitationem ulla</p>
</div>
<div class="service" style="left:103px;top:1254px">
  <svg viewBox="0 0 64 64"><path d="M44 12H10v44h44V30"/><path d="M26 40l4-10 22-22 6 6-22 22z"/></svg>
  <h3>Inventory</h3><p>Ut enim ad minima veniam quis nostrum exercitationem ulla</p>
</div>
<div class="service" style="left:355px;top:1254px">
  <svg viewBox="0 0 64 64"><path d="M6 56h52M6 8v48"/><rect x="14" y="36" width="7" height="16"/><rect x="26" y="26" width="7" height="26"/><rect x="38" y="30" width="7" height="22"/><rect x="50" y="16" width="7" height="36"/></svg>
  <h3>Equipment Financing</h3><p>Ut enim ad minima veniam quis nostrum exercitationem ulla</p>
</div>
<div class="service" style="left:605px;top:1254px">
  <svg viewBox="0 0 64 64"><circle cx="32" cy="14" r="7"/><circle cx="16" cy="34" r="6"/><circle cx="48" cy="34" r="6"/><path d="M20 30a12 10 0 0 1 24 0M4 56a12 11 0 0 1 24 0M36 56a12 11 0 0 1 24 0"/></svg>
  <h3>Business Acquisitions</h3><p>Ut enim ad minima veniam quis nostrum exercitationem ulla</p>
</div>
<div class="service" style="left:861px;top:1254px">
  <svg viewBox="0 0 64 64"><rect x="22" y="22" width="20" height="20"/><path d="M6 6l14 14M58 6L44 20M6 58l14-14M58 58L44 44M6 6h10M6 6v10M58 6H48M58 6v10M6 58h10M6 58V48M58 58H48M58 58V48"/></svg>
  <h3>Business Expansion</h3><p>Ut enim ad minima veniam quis nostrum exercitationem ulla</p>
</div>
<div class="btn-outline" style="left:505px;top:1511px">VIEW MORE</div>

<section class="about">
  <h2 class="serif">ABOUT US</h2>
  <p>Nemo enim ipsam voluptatem quia voluptas sit aspernatur aut odit aut fugit, sed quia consequuntur magni dolores eos qui ratione voluptatem sequi nesciunt. Neque porro quisquam est, qui dolorem ipsum quia dolor sit amet, consectetur, adipisci velit, sed quia non numquam eius modi tempora incidunt ut lab.</p>
  <div class="btn-small">READ MORE</div>
  <div class="photo" role="img" aria-label="Hands holding a smartphone with glowing financial data overlays"></div>
</section>

<h2 class="section-title serif" style="top:2228px">LOAN PROGRAMS</h2>
<div class="loan-photo" style="left:0;top:2357px;width:392px;background:linear-gradient(180deg,#8fb3dc 0%,#c8dbea 45%,#8c8a4e 62%,#6f6a38 100%)" role="img" aria-label="Open grassland field under a blue sky"></div>
<div class="loan-photo" style="left:402px;top:2357px;width:396px;background:linear-gradient(180deg,#b9a88f 0%,#d9cfc1 50%,#9a8a74 100%)" role="img" aria-label="Hotel lobby with reception desk"></div>
<div class="loan-photo" style="left:804px;top:2357px;width:396px;background:linear-gradient(180deg,#8fb2d8 0%,#c7bfae 45%,#6d6a66 75%,#4b4b4b 100%)" role="img" aria-label="Multifamily apartment buildings with parking"></div>
<div class="loan-label serif" style="left:0;top:2664px">LAND LOANS</div>
<div class="loan-label serif" style="left:402px;top:2664px">HOSPITALITY LOANS</div>
<div class="loan-label serif" style="left:804px;top:2664px">MULTIFAMILY LOANS</div>
<div class="loan-photo" style="left:0;top:2742px;width:392px;background:linear-gradient(180deg,#eeeeee 0%,#d6d6d6 60%,#a7a7a7 100%)" role="img" aria-label="Bright modern office interior"></div>
<div class="loan-photo" style="left:402px;top:2742px;width:396px;background:linear-gradient(180deg,#d8dde2 0%,#eef0f2 50%,#b8bec4 100%)" role="img" aria-label="Retail shopping mall interior"></div>
<div class="loan-photo" style="left:804px;top:2742px;width:396px;background:linear-gradient(180deg,#9ebde0 0%,#b6c2cc 50%,#7b7f82 100%)" role="img" aria-label="Industrial warehouse building"></div>
<div class="loan-label serif" style="left:0;top:3050px">OFFICE LOANS</div>
<div class="loan-label serif" style="left:402px;top:3050px">RETAIL LOANS</div>
<div class="loan-label serif" style="left:804px;top:3050px">INDUSTRIAL LOANS</div>
<div class="btn-outline" style="left:505px;top:3148px">VIEW MORE</div>

<section class="apply">
  <h2 class="serif">APPLY NOW</h2>
  <div class="lead">Ready to turn your plans into action?</div>
  <div class="field">Email Address</div>
  <div class="go"><svg width="28" height="18" viewBox="0 0 28 18" fill="none" stroke="#fff" stroke-width="3"><path d="M2 9h22M16 2l8 7-8 7"/></svg></div>
</section>

<h2 class="section-title serif" style="top:3834px">OUR TEAM</h2>
<div class="member" style="left:98px;top:3942px"><div class="avatar" role="img" aria-label="Headshot of team member"></div><h3>Daniel Reyes</h3><div class="role">Manager</div><p>Sequuntur magni dolores eos qui ratione voluptatem sequi nes ciunue porro quisquam</p></div>
<div class="member" style="left:350px;top:3942px"><div class="avatar" role="img" aria-label="Headshot of team member"></div><h3>Marissa</h3><div class="role">Manager</div><p>Sequuntur magni dolores eos qui ratione voluptatem sequi nes ciunue porro quisquam</p></div>
<div class="member" style="left:600px;top:3942px"><div class="avatar" role="img" aria-label="Headshot of team member"></div><h3>Thomas</h3><div class="role">Manager</div><p>Sequuntur magni dolores eos qui ratione voluptatem sequi nes ciunue porro quisquam</p></div>
<div class="member" style="left:852px;top:3942px"><div class="avatar" role="img" aria-label="Headshot of team member"></div><h3>Helena</h3><div class="role">Manager</div><p>Sequuntur magni dolores eos qui ratione voluptatem sequi nes ciunue porro quisquam</p></div>

<footer class="site-footer">
  <h4 style="left:113px">CONTACT FORM</h4>
  <h4 style="left:801px">CONTACT INFORMATION</h4>
  <div class="input" style="left:113px;top:179px;width:308px">First Name</div>
  <div class="input" style="left:431px;top:179px;width:310px">Last Name</div>
  <div class="input" style="left:113px;top:226px;width:308px">Email</div>
  <div class="input" style="left:431px;top:226px;width:310px">Phone Number</div>
  <div class="input textarea" style="left:113px;top:269px;width:628px;height:83px">Comments</div>
  <div class="submit">SUBMIT</div>

  <div class="info" style="top:168px"><span class="ring"><svg viewBox="0 0 24 24"><path d="M12 2a7 7 0 0 0-7 7c0 5 7 13 7 13s7-8 7-13a7 7 0 0 0-7-7zm0 9.5A2.5 2.5 0 1 1 12 6.5a2.5 2.5 0 0 1 0 5z"/></svg></span><span>218 Harlow Creek Rd. Ste 400<br>Brenton, Pa 19340 Usa</span></div>
  <div class="info" style="top:233px"><span class="ring"><svg viewBox="0 0 24 24"><path d="M6.6 10.8a15 15 0 0 0 6.6 6.6l2.2-2.2c.3-.3.7-.4 1-.2 1.1.4 2.3.6 3.6.6.6 0 1 .4 1 1V20c0 .6-.4 1-1 1A17 17 0 0 1 3 4c0-.6.4-1 1-1h3.5c.6 0 1 .4 1 1 0 1.3.2 2.5.6 3.6.1.3 0 .7-.2 1z"/></svg></span><span>1 800 555 0142</span></div>
  <div class="info" style="top:296px"><span class="ring"><svg viewBox="0 0 24 24"><path d="M2 5h20v14H2z"/><path d="M3 6l9 7 9-7" stroke="#0d0d0d" stroke-width="1.6" fill="none"/></svg></span><span>info@corvanelending.com</span></div>
  <div class="social"><span></span><span></span><span></span><span></span></div>
  <div class="rule"></div>
  <div class="copy">Copyright © 2018, Corvane. All rights reserved.</div>
</footer>

</body>
</html>
```